*YO!!! Designers Needed!!* Front Page Cover Needed for a $$Billion Dollar$$ Company

We are a manufacturer of aluminum electrolytic capacitors. We are looking to create a front page cover that will be used on our annual report. We are a publicly listed company and work with many Meridex 400 companies, so your work will be viewed by the BIG GUNS and EXECUTIVES around the WORLD! If selected, you may be selected for additional work.

The front page cover should be unique. If elegance, modern, bling, and creativity somehow got together and had a child, that's what the cover page would look like!

Inspired Examples attached. Check them out!

www.brovanta.com

Font styles to use
Sans Serif

Requirements
Must have
• 1. Must include the attached logo. Logo size, color, and placement are at your discretion.

2. Should include the text, '2020 Annual Report'

3. The design should incorporate the use of foil and/or be embossed. The foil can be part of the design or can be the full page. See various examples attached for reference.

4. Shall be in A4 size and vertical orientation.
Nice to have
• Feel free to add any icons or stock photos (for example capacitors or circuit boards) if needed.

Be creative here and don't be afraid to be bold! The end product will be printed and budget is not a limiting factor, so feel free to make it extravagant if needed.

Our slogan is "Think Ahead". This slogan can or cannot be part of the theme.

```html
<!DOCTYPE html>
<html lang="en">
<head>
<meta charset="utf-8">
<title>Brovanta Annual Report 2020 Cover</title>
<link rel="stylesheet" href="https://fonts.googleapis.com/css2?family=Josefin+Sans:wght@400;600;700&display=swap">
<style>
  :root {
    --backdrop: #1c1c1c;
    --paper: #efeee9;
    --paper-shade: #e9e7e1;
    --bronze: #7b5634;
    --cream: #f3ece2;
  }
  * { margin: 0; padding: 0; box-sizing: border-box; }
  html, body {
    width: 1124px;
    height: 1200px;
    overflow: hidden;
    background: var(--backdrop);
  }
  .cover {
    position: absolute;
    left: 166px;
    top: 40px;
    width: 792px;
    height: 1120px;
    background: var(--paper);
    font-family: "Josefin Sans", sans-serif;
    color: var(--bronze);
    overflow: hidden;
  }
  .cover__artwork {
    position: absolute;
    left: 300px;
    top: 270px;
    width: 440px;
    height: 780px;
    background: linear-gradient(160deg, var(--paper) 0%, var(--paper-shade) 50%, var(--paper) 100%);
    opacity: 0.5;
  }
  .brand {
    position: absolute;
    left: 0;
    top: 112px;
    width: 100%;
    text-align: center;
  }
  .brand__name {
    display: block;
    font-size: 100px;
    font-weight: 700;
    line-height: 1;
    letter-spacing: 2px;
  }
  .title {
    position: absolute;
    left: 0;
    width: 100%;
    text-align: center;
    font-weight: 600;
    line-height: 1;
    text-transform: uppercase;
    font-size: 150px;
  }
  .title--annual { top: 542px; letter-spacing: 0; }
  .title--report { top: 680px; letter-spacing: 0; }
  .year {
    position: absolute;
    left: 0;
    top: 808px;
    width: 100%;
    height: 90px;
  }
  .year__digits {
    position: absolute;
    left: 0;
    top: 8px;
    width: 100%;
    text-align: center;
    font-size: 96px;
    font-weight: 600;
    line-height: 1;
    letter-spacing: 28px;
    padding-left: 28px;
    transform: scaleX(0.78);
  }
  .year__rule { position: absolute; top: 28px; }
  .year__rule--left { left: 134px; }
  .year__rule--right { right: 134px; transform: scaleX(-1); }
  .web-band {
    position: absolute;
    left: 0;
    top: 964px;
    width: 100%;
    height: 82px;
    background: var(--bronze);
    display: flex;
    align-items: center;
    justify-content: center;
  }
  .web-band__address {
    color: var(--cream);
    font-size: 21px;
    font-weight: 400;
    letter-spacing: 8px;
    text-transform: uppercase;
    padding-top: 4px;
  }
</style>
</head>
<body>
  <main class="cover">
    <div class="cover__artwork" role="img" aria-label="Faint blind-embossed illustration of capacitors"></div>

    <header class="brand">
      <span class="brand__name">Brovanta</span>
    </header>

    <h1>
      <span class="title title--annual">Annual</span>
      <span class="title title--report">Report</span>
    </h1>

    <div class="year">
      <svg class="year__rule year__rule--left" width="112" height="28" viewBox="0 0 112 28">
        <rect x="0" y="0" width="112" height="4" fill="#7b5634"/>
        <rect x="26" y="10" width="86" height="4" fill="#7b5634"/>
        <rect x="56" y="20" width="56" height="4" fill="#7b5634"/>
      </svg>
      <span class="year__digits">2020</span>
      <svg class="year__rule year__rule--right" width="112" height="28" viewBox="0 0 112 28">
        <rect x="0" y="0" width="112" height="4" fill="#7b5634"/>
        <rect x="26" y="10" width="86" height="4" fill="#7b5634"/>
        <rect x="56" y="20" width="56" height="4" fill="#7b5634"/>
      </svg>
    </div>

    <footer class="web-band">
      <span class="web-band__address">www.brovanta.com</span>
    </footer>
  </main>
</body>
</html>
```